Business card for Luxury Portable Restroom Trailer company

We are a Luxury Portable Restroom Trailer Company Called FALCRIDGE HIRES. Based in Orange County California. We provide portable restroom trailers for events, such as, Weddings, Concerts, Charity events, Sporting events, Tournaments, Corporate events, ect. We rent and Sell the Luxury restrooms. Our colors are white, grey, and Orange. As you will see in the logo we uploaded.
There are 2 people in the company so the names and titles will change for the 3 people but card will remain the same. Here is the information for each Person: Dwight Penner CFO 555 318-0476
next Person: Leon Marchetti VP 555 318-0476
Next Person: Owen Marchetti CEO 555 318-0476
Information to include on the card: Luxury Restroom Trailers Rental and Sales. Weddings, Concerts, Charity, Sporting and Corp. Events.

```html
<!DOCTYPE html>
<html lang="en">
<head>
<meta charset="utf-8">
<title>Falcridge Hires — Business Card</title>
<link rel="stylesheet" href="https://fonts.googleapis.com/css2?family=Montserrat:wght@400;500;700;800&display=swap">
<style>
  :root {
    --orange: #ec6a22;
    --grey-band: #58585b;
    --grey-back: #555558;
    --ink: #3f3f42;
    --paper: #ffffff;
    --stage: #2a2a2c;
  }
  * { margin: 0; padding: 0; box-sizing: border-box; }
  html, body {
    width: 1200px; height: 878px; overflow: hidden;
    background: var(--stage);
    font-family: "Montserrat", sans-serif;
  }
  .canvas { position: relative; width: 1200px; height: 878px; }

  .card {
    position: absolute; left: 250px; width: 700px; height: 400px;
    overflow: hidden;
  }
  .card--front { top: 24px; background: var(--paper); }
  .card--back { top: 454px; background: var(--grey-back); }

  /* front: brand */
  .brand {
    position: absolute; left: 44px; top: 178px;
    display: flex; align-items: center; gap: 12px;
  }
  .brand__dot {
    width: 34px; height: 34px; border-radius: 50%;
    background: var(--orange);
  }
  .brand__name {
    font-weight: 800; font-size: 23px; letter-spacing: 0.5px;
    color: var(--orange); white-space: nowrap;
  }

  .divider {
    position: absolute; left: 352px; top: 122px;
    width: 2px; height: 150px; background: var(--orange);
  }

  /* front: person */
  .person { position: absolute; left: 384px; top: 118px; }
  .person__name {
    font-weight: 800; font-size: 26px; letter-spacing: 1.2px;
    color: var(--orange); text-transform: uppercase; line-height: 1.1;
    white-space: nowrap;
  }
  .person__title {
    font-weight: 500; font-size: 15px; letter-spacing: 1px;
    color: var(--ink); margin-top: 2px;
  }

  .contacts {
    position: absolute; left: 384px; top: 190px;
    list-style: none;
  }
  .contacts__item {
    display: flex; align-items: center; gap: 10px;
    font-size: 16px; letter-spacing: 0.6px; color: var(--ink);
    height: 27px; white-space: nowrap;
  }
  .contacts__icon { width: 14px; height: 14px; flex: none; }

  /* front: footer band */
  .rule {
    position: absolute; left: 0; top: 300px;
    width: 100%; height: 4px; background: var(--orange);
  }
  .band {
    position: absolute; left: 0; top: 310px;
    width: 100%; height: 90px; background: var(--grey-band);
    text-align: center; padding-top: 16px;
  }
  .band__tagline {
    font-weight: 700; font-size: 15px; letter-spacing: 0.8px;
    color: var(--orange);
  }
  .band__services {
    font-weight: 500; font-size: 18px; letter-spacing: 0.8px;
    color: #ffffff; margin-top: 8px;
  }

  /* back */
  .back__pattern {
    position: absolute; inset: 0;
    background: linear-gradient(135deg, #5a5a5d, #4e4e51);
  }
  .back__ring {
    position: absolute; left: 566px; top: 150px;
    width: 60px; height: 60px; border-radius: 50%;
    border: 4px solid var(--orange);
  }
</style>
</head>
<body>
<main class="canvas">

  <section class="card card--front" aria-label="Business card front">
    <div class="brand">
      <span class="brand__dot"></span>
      <span class="brand__name">FALCRIDGE HIRES</span>
    </div>

    <div class="divider"></div>

    <div class="person">
      <h1 class="person__name">Owen Marchetti</h1>
      <p class="person__title">CEO</p>
    </div>

    <ul class="contacts">
      <li class="contacts__item">
        <svg class="contacts__icon" viewBox="0 0 24 24" aria-hidden="true">
          <path fill="var(--orange)" d="M6.6 10.8a15.1 15.1 0 0 0 6.6 6.6l2.2-2.2c.3-.3.7-.4 1-.2 1.1.4 2.3.6 3.6.6.6 0 1 .4 1 1V20c0 .6-.4 1-1 1A17 17 0 0 1 3 4c0-.6.4-1 1-1h3.5c.6 0 1 .4 1 1 0 1.3.2 2.5.6 3.6.1.3 0 .7-.2 1z"/>
        </svg>
        <span>555 318-0476</span>
      </li>
      <li class="contacts__item">
        <svg class="contacts__icon" viewBox="0 0 24 24" aria-hidden="true">
          <rect x="2" y="5" width="20" height="14" rx="1.5" fill="var(--orange)"/>
          <path d="M3 6l9 7 9-7" fill="none" stroke="#fff" stroke-width="1.8"/>
        </svg>
        <span>team@falcridgehires.com</span>
      </li>
      <li class="contacts__item">
        <svg class="contacts__icon" viewBox="0 0 24 24" aria-hidden="true">
          <circle cx="12" cy="12" r="10" fill="var(--orange)"/>
          <path d="M2 12h20M12 2c3 3 3 17 0 20M12 2c-3 3-3 17 0 20" fill="none" stroke="#fff" stroke-width="1.4"/>
        </svg>
        <span>www.falcridgehires.com</span>
      </li>
    </ul>

    <div class="rule"></div>
    <div class="band">
      <p class="band__tagline">Luxury Restroom Trailers Rental and Sales</p>
      <p class="band__services">Weddings | Concerts | Charity | Sporting | Corp</p>
    </div>
  </section>

  <section class="card card--back" aria-label="Business card back">
    <div class="back__pattern" role="img" aria-label="Repeating embossed brand mark pattern in dark grey tones"></div>
    <div class="back__ring"></div>
  </section>

</main>
</body>
</html>
```